website design for M&T Electric

A portfolio website for a high end commercial and residential electrical contracting company. The current site mandtelectric.example does not represent the current direction but the images in the gallery give you an idea of the work we do. Current logo will be uploaded shortly but is black text on white background.
Target Market(s)
General Contractors, Residential Home Owners, clients intersted in Velmora home automation.
Industry/Entity Type
Electrician
Coding
Coded - Design and coding required
Number of Pages Required
2 page
Font styles to use
Sans Serif
Colors
Designer to choose colors to be used in the design.
Requirements
Must have
- Portfolio section highlighting different service areas and products (Velmora Housepilot, etc)

```html
<!DOCTYPE html>
<html lang="en">
<head>
<meta charset="utf-8">
<title>M&amp;T Electric</title>
<link href="https://fonts.googleapis.com/css2?family=Open+Sans:wght@400;600&family=Raleway:wght@400;500;600;700&display=swap" rel="stylesheet">
<style>
:root{
  --gold:#d6a30b;
  --gold-dark:#c4940a;
  --ink:#1d1d1d;
  --dark:#1b1b1b;
  --text:#333;
  --muted:#bdbdbd;
  --white:#fff;
}
*{margin:0;padding:0;box-sizing:border-box}
html,body{width:1200px;height:2332px;overflow:hidden}
body{font-family:"Open Sans",sans-serif;color:var(--text);background:var(--white);position:relative}
.header{position:absolute;left:0;top:0;width:1200px;height:80px;background:linear-gradient(#2a2a2a,#0c0c0c)}
.logo{position:absolute;left:160px;top:16px;font-family:"Raleway",sans-serif;font-weight:400;font-size:40px;color:var(--white);letter-spacing:1px}
.nav{position:absolute;right:162px;top:33px;display:flex;gap:32px;font-family:"Raleway",sans-serif;font-size:12px;letter-spacing:1.2px;color:#aaa;align-items:center}
.nav .active{color:var(--white)}
.hero{position:absolute;left:0;top:80px;width:1200px;height:489px}
.hero-backdrop{position:absolute;inset:0;background:linear-gradient(100deg,rgba(0,0,0,.15) 0%,rgba(0,0,0,0) 45%,rgba(0,0,0,.25) 100%),linear-gradient(180deg,#55637a 0%,#b48470 32%,#6d6c62 58%,#3e5229 78%,#2c3b1d 100%)}
.hero h1{position:absolute;left:160px;top:178px;font-family:"Raleway",sans-serif;font-weight:500;font-size:46px;color:var(--white)}
.hero p{position:absolute;left:160px;top:244px;font-family:"Raleway",sans-serif;font-weight:500;font-size:20px;line-height:29px;color:#f0d48a}
.dots{position:absolute;left:532px;top:442px;display:flex;gap:6px}
.dots span{width:30px;height:3px;background:rgba(255,255,255,.55)}
.dots span:first-child{background:var(--white)}
.services-title{position:absolute;top:614px;width:1200px;text-align:center;font-family:"Raleway",sans-serif;font-weight:700;font-size:20px;color:var(--ink)}
.services-intro{position:absolute;left:180px;top:662px;width:840px;text-align:center;font-size:10.5px;line-height:21px;color:#222}
.grid{position:absolute;left:162px;top:763px;display:grid;grid-template-columns:repeat(4,205px);column-gap:19px;row-gap:20px}
.card{width:205px;height:188px}
.card .photo{height:132px}
.card .bar{height:56px;background:var(--gold);display:flex;align-items:center;justify-content:space-between;padding:0 14px;font-family:"Raleway",sans-serif;font-weight:700;font-size:12px;color:var(--white)}
.recent{position:absolute;left:0;top:1237px;width:603px;height:403px;background:var(--dark)}
.recent h2{position:absolute;left:162px;top:75px;font-family:"Raleway",sans-serif;font-weight:700;font-size:19px;color:var(--white)}
.recent p{position:absolute;left:162px;top:117px;width:402px;font-size:10.3px;line-height:20px;color:#e6e6e6;text-align:justify}
.btn-solid{position:absolute;left:162px;top:318px;width:134px;height:38px;border-radius:19px;background:var(--gold);color:var(--white);font-family:"Raleway",sans-serif;font-weight:700;font-size:11px;display:flex;align-items:center;justify-content:center}
.recent-photo{position:absolute;left:603px;top:1237px;width:597px;height:403px;background:linear-gradient(180deg,#4a2e1e 0%,#b9a690 40%,#d8cbb8 70%,#8c7a68 100%)}
.news-title{position:absolute;left:162px;top:1692px;font-family:"Raleway",sans-serif;font-weight:700;font-size:19px;color:var(--ink)}
.news{position:absolute;top:1763px;width:240px}
.news .date{position:absolute;left:0;top:3px;width:42px;border-right:2px solid #ccc;font-family:"Raleway",sans-serif;color:var(--gold);line-height:1}
.news .date .m{font-size:14px;display:block}
.news .date .d{font-size:25px;font-weight:700;display:block}
.news h3{position:absolute;left:64px;top:0;width:180px;font-family:"Raleway",sans-serif;font-weight:500;font-size:16px;line-height:23px;color:var(--ink)}
.news p{position:absolute;left:0;top:62px;width:240px;font-size:11px;line-height:20px;color:#333}
.btn-outline{position:absolute;left:0;top:164px;width:88px;height:28px;border:1.5px solid var(--gold);border-radius:14px;color:var(--gold-dark);font-family:"Raleway",sans-serif;font-weight:700;font-size:10px;display:flex;align-items:center;justify-content:center}
.footer{position:absolute;left:0;top:2020px;width:1200px;height:312px;background:linear-gradient(#2a2a2a,#141414);color:var(--muted)}
.fcol{position:absolute;top:55px}
.fcol h4{font-family:"Raleway",sans-serif;font-weight:600;font-size:14px;color:var(--white);margin-bottom:14px}
.fcol li{list-style:none;font-size:11px;line-height:21px}
.social{display:flex;gap:4px}
.social span{width:32px;height:32px;border:1.5px solid var(--white);border-radius:50%}
.copy{position:absolute;top:270px;width:1200px;text-align:center;font-size:10.5px;color:var(--white)}
</style>
</head>
<body>
<header class="header">
  <div class="logo">M&amp;T Electric</div>
  <nav class="nav">
    <span class="active">HOME</span><span>GALLERY</span><span>SPECIALTY SERVICES</span><span>ABOUT</span><span>CONTACT</span>
    <svg width="12" height="12" viewBox="0 0 12 12"><circle cx="5" cy="5" r="3.5" fill="none" stroke="#fff" stroke-width="1.6"/><line x1="7.6" y1="7.6" x2="11" y2="11" stroke="#fff" stroke-width="1.8"/></svg>
  </nav>
</header>

<section class="hero">
  <div class="hero-backdrop" role="img" aria-label="Modern gabled house lit warmly at dusk on a green lawn"></div>
  <h1>M&amp;T Electric</h1>
  <p>Commercial and Residential<br>Electrical contracting company</p>
  <div class="dots"><span></span><span></span><span></span><span></span></div>
</section>

<h2 class="services-title">M &amp; T ELECTRIC SERVICES</h2>
<p class="services-intro">Lorem ipsum dolor sit amet, consectetur adipiscing elit, sed do eiusmod tempor incididunt ut labore et dolore magna aliquat enim ad minim veniam, quis exercitation ullamco labo ris nisi ut aliquip ex ea commodo consequat. Duis aute irure dolor in reprehenderit in voluptate orem ipsum dolor sit amet, consctetur adipiscing elit, sed do eiusmod tempor incididunt ut labore et dolore magna aliquaenim ad minim veniam, quis nostrud exercitation ullamco labo.</p>

<div class="grid">
  <div class="card"><div class="photo" role="img" aria-label="Commercial building lit at dusk" style="background:linear-gradient(#2a4a8a,#5a5048)"></div><div class="bar">COMMERCIAL<span>›</span></div></div>
  <div class="card"><div class="photo" role="img" aria-label="Residential hallway with pendant light" style="background:linear-gradient(#6a4a30,#c8a880)"></div><div class="bar">RESIDENTIAL<span>›</span></div></div>
  <div class="card"><div class="photo" role="img" aria-label="Home with landscape lighting at night" style="background:linear-gradient(#0e1422,#5a4030)"></div><div class="bar">LANDSCAPE<span>›</span></div></div>
  <div class="card"><div class="photo" role="img" aria-label="Standby generator unit beside a house" style="background:linear-gradient(#8a7a6e,#d8d8d8)"></div><div class="bar">GENERATORS<span>›</span></div></div>
  <div class="card"><div class="photo" role="img" aria-label="Living room with large windows and shades" style="background:linear-gradient(#3a3a3a,#8a8a90)"></div><div class="bar">VELMORA SHADES<span>›</span></div></div>
  <div class="card"><div class="photo" role="img" aria-label="White kitchen with dimmable pendant lights" style="background:linear-gradient(#e8e8e8,#a8a8a8)"></div><div class="bar">VELMORA DIMMING<span>›</span></div></div>
  <div class="card"><div class="photo" role="img" aria-label="Glowing LED bulb among other bulbs" style="background:linear-gradient(#3a5a80,#b8c8dc)"></div><div class="bar">LED LIGHTING<span>›</span></div></div>
  <div class="card"><div class="photo" role="img" aria-label="Electrician arriving for a service call" style="background:linear-gradient(#5a6a4a,#2a3a6a)"></div><div class="bar">SERVICE CALLS<span>›</span></div></div>
</div>

<section class="recent">
  <h2>RECENT WORK</h2>
  <p>Lorem ipsum dolor sit amet, consectetur adipiscing elit, sed do eiusmod tempor incididunt ut labore et dolore magna aliquat enim ad minim veniam, quis nostrud exercitation ullamco labo ris nisi ut aliquip ex ea commodo consequat. Duis aute irure dolor in reprehenderit in voluptate orem ipsum dolor sit amet, consectetur adipiscing elit, sed do eiusmod tempor incididunt ut labore et dolore magna aliqua. Ut enim ad minim veniam, quis nostrud exercitation ullamco laboris nisi ut aliquip ex ea commodo consequat.uis aute irure dolorrcitation ullamco laboris nisi ut aliquip ex ea commodo consequat.uis aute irure dolor.</p>
  <div class="btn-solid">MORE WORKS</div>
</section>
<div class="recent-photo" role="img" aria-label="Hotel lobby with chandeliers and polished marble floor"></div>

<h2 class="news-title">LATEST NEWS</h2>
<article class="news" style="left:162px">
  <div class="date"><span class="m">MAY</span><span class="d">20</span></div>
  <h3>Lorem ipsum dolor sit ametonsectetur.</h3>
  <p>Sd ut perspiciatis unde omnis isteiste natrort vo luptatem accusantium doloremque lisuertis un de omnis isteiste natus Sed ut persluptmus antium doloremque lisut persnis.</p>
  <div class="btn-outline">READ MORE</div>
</article>
<article class="news" style="left:486px">
  <div class="date"><span class="m">MAY</span><span class="d">20</span></div>
  <h3>Lorem ipsum dolor sit ametonsectetur.</h3>
  <p>Sd ut perspiciatis unde omnis isteiste natrort vo luptatem accusantium doloremque lisuertis un de omnis isteiste natus Sed ut persluptus antium doloremque lisut persnis.</p>
  <div class="btn-outline">READ MORE</div>
</article>
<article class="news" style="left:810px">
  <div class="date"><span class="m">MAY</span><span class="d">20</span></div>
  <h3>Lorem ipsum dolor sit ametonsectetur.</h3>
  <p>Sd ut perspiciatis unde omnis isteiste natrort vo luptatem accusantium doloremque lisuertis un de omnis isteiste natus Sed ut persluptus antium doloremque lisut persnis.</p>
  <div class="btn-outline">READ MORE</div>
</article>

<footer class="footer">
  <div class="fcol" style="left:162px"><h4>Follow US</h4>
    <div class="social"><span aria-label="Social profile"></span><span aria-label="Social profile"></span><span aria-label="Social profile"></span><span aria-label="Social profile"></span></div>
  </div>
  <div class="fcol" style="left:398px"><h4>Help Us</h4><ul><li>Commercial</li><li>Residential</li><li>Landscape</li><li>Specialty Services</li><li>Velmora Shades</li><li>Generators</li></ul></div>
  <div class="fcol" style="left:564px"><h4>Links</h4><ul><li>Privacy Policy</li><li>Cookies *</li><li>Terms of Use</li><li>Disclaimer</li><li>Legal</li></ul></div>
  <div class="fcol" style="left:733px"><h4>Company</h4><ul><li>Home</li><li>Gallery</li><li>Specialty Services</li><li>About</li><li>Contact</li></ul></div>
  <div class="fcol" style="left:884px"><h4>Help &amp; Contact</h4><ul><li>2187 Cedar Field Rd PO Box 5120</li><li>Pinecrest, ID 83999</li><li>Phone: (208) 555-0147</li><li>dmercer@mandtelectric.example</li><li>cwalsh@mandtelectric.example</li></ul></div>
  <div class="copy">© 2017 Mandtelectric. All Copyrights are Reserved. Terms and Conditions &nbsp;&nbsp;&nbsp;|&nbsp;&nbsp;&nbsp; Schedule Estimate</div>
</footer>
</body>
</html>
```